Business card for a Exhibition booth fabrication company

Hi. My company would like to change our corporate name card. We are an events and Exhibition stand builder company. We would like our corporate name card to resonate what we do. I need someone to create something unique that relates to the industry that I am in. The graphic designer should be creative to incorporate the elements of my industry and try to blend in well in the design of the card. Our aim is to ensure that we are unique and our card can look different from our competitors.
Updates

Target Market(s)

Marketing and events manager from all companies

Contact Information for Business Card

The business card should have the following details:
Name
Job Title
Email
Website

Colors

Designer to choose colors to be used in the design.

Requirements
Must have
• The card must be look something that is relevant to the service that I am providing. My website is: www.velmora-buildworks.com
• You can see my website to get more information on what service that I am doing
Nice to have
• On the back of my card, I would like to have a globe image with the incorporation of my company logo. This is to indicate that my services can be done in any part of the world.

```html
<!DOCTYPE html>
<html lang="en">
<head>
<meta charset="UTF-8">
<title>Velmora Buildworks – Business Card</title>
<link rel="stylesheet" href="https://fonts.googleapis.com/css2?family=Montserrat:wght@600&family=Open+Sans:wght@400;700;800&family=Merriweather:wght@400&display=swap">
<style>
  :root {
    --bg: #3a3f47;
    --card: #ffffff;
    --red: #e21f2a;
    --charcoal: #3b3b3d;
    --ink: #2c2c2e;
    --grey-name: #5a5656;
    --map-light: #e6e6e6;
    --map-mid: #cfcfcf;
  }
  * { margin: 0; padding: 0; box-sizing: border-box; }
  html, body { width: 1200px; height: 1200px; overflow: hidden; }
  body {
    background: var(--bg);
    display: flex;
    flex-direction: column;
    align-items: center;
    justify-content: center;
    gap: 60px;
    font-family: "Open Sans", sans-serif;
  }
  .card {
    position: relative;
    width: 840px;
    height: 480px;
    background: var(--card);
    overflow: hidden;
    box-shadow: 0 10px 30px rgba(0,0,0,0.35);
  }
  .card__shapes { position: absolute; inset: 0; width: 100%; height: 100%; }

  /* Back */
  .world-map {
    position: absolute;
    left: 300px; top: 50px;
    width: 500px; height: 380px;
    border-radius: 50% 50% 42% 42%;
    background: radial-gradient(ellipse at 50% 45%, var(--map-mid) 0%, var(--map-light) 55%, rgba(255,255,255,0) 75%);
  }
  .brand {
    position: absolute;
    display: flex;
    align-items: center;
    gap: 16px;
  }
  .brand__dot {
    width: 30px; height: 30px;
    border-radius: 50%;
    background: var(--red);
    flex: none;
  }
  .brand__name {
    font-family: "Montserrat", sans-serif;
    font-weight: 600;
    color: var(--ink);
    letter-spacing: 0.12em;
    text-transform: uppercase;
    white-space: nowrap;
  }
  .card--back .brand { left: 150px; top: 218px; }
  .card--back .brand__name { font-size: 34px; }

  /* Front */
  .card--front .brand { right: 60px; top: 150px; }
  .card--front .brand__name { font-size: 24px; }
  .person {
    position: absolute;
    left: 62px; top: 150px;
  }
  .person__name {
    font-weight: 800;
    font-size: 38px;
    line-height: 1;
    color: var(--grey-name);
  }
  .person__first { color: var(--red); }
  .person__title {
    font-family: "Merriweather", serif;
    font-size: 19px;
    color: var(--ink);
    margin-top: 8px;
  }
  .person__rule {
    width: 34px; height: 3px;
    background: var(--red);
    margin-top: 8px;
  }
  .contact {
    list-style: none;
    margin-top: 14px;
    font-size: 19px;
    color: var(--ink);
  }
  .contact li { display: flex; align-items: center; gap: 10px; line-height: 1.45; }
  .contact svg { width: 20px; height: 20px; flex: none; }
</style>
</head>
<body>

  <section class="card card--back" aria-label="Business card back">
    <div class="world-map" role="img" aria-label="Faint grey world map showing the company works worldwide"></div>
    <div class="brand">
      <span class="brand__dot"></span>
      <span class="brand__name">Velmora Buildworks</span>
    </div>
  </section>

  <section class="card card--front" aria-label="Business card front">
    <svg class="card__shapes" viewBox="0 0 840 480" aria-hidden="true">
      <polygon points="0,6 30,6 0,40" fill="var(--charcoal)"/>
      <polygon points="60,0 100,0 18,108 0,108 0,80" fill="var(--charcoal)" transform="translate(-10,0)"/>
      <polygon points="120,0 180,0 70,120 40,120" fill="var(--red)" transform="translate(-40,0)"/>
      <polygon points="840,300 840,360 770,480 720,480" fill="var(--red)"/>
      <polygon points="840,400 840,440 818,480 790,480" fill="var(--charcoal)"/>
    </svg>

    <div class="person">
      <h1 class="person__name"><span class="person__first">Daniel</span> Reyes</h1>
      <p class="person__title">Director</p>
      <div class="person__rule"></div>
      <ul class="contact">
        <li>
          <svg viewBox="0 0 20 20" aria-hidden="true"><rect x="1" y="4" width="18" height="12" rx="2" fill="var(--red)"/><path d="M2 5 L10 11 L18 5" stroke="#fff" stroke-width="1.6" fill="none"/></svg>
          username@velmora-buildworks.com
        </li>
        <li>
          <svg viewBox="0 0 20 20" aria-hidden="true"><circle cx="10" cy="10" r="9" fill="var(--red)"/><path d="M1.5 10h17M10 1.5v17M4 5.5h12M4 14.5h12" stroke="#fff" stroke-width="1.2" fill="none"/><ellipse cx="10" cy="10" rx="4" ry="8.5" stroke="#fff" stroke-width="1.2" fill="none"/></svg>
          www.velmora-buildworks.com
        </li>
      </ul>
    </div>

    <div class="brand">
      <span class="brand__dot"></span>
      <span class="brand__name">Velmora Buildworks</span>
    </div>
  </section>

</body>
</html>
```